Webshop for furniture and lamps

We need a design for a web shop with APP that should have two options:
1-Webshop in general which should attract to private customer in general and
2-Website that is meant to attract big customers as hotels and restaurants who would have their own customerize login.

That's the idea behind the shop.

It should be diveded into 4 parts
vintage furniture
rattan set outdoor and indoor
lamps and
wooden wall decor

The name of the shop is loma vereda!

Please kindly make me an offer.

Reason: Dear designers, so far there hasn't been a design that really matched. Look up German web sites like www.glimmerhof-wohnen.de or www.sitzraum77.de... Haven't been convinced by designs! Sorry folks. Please submit some new ones. Kind regards Ned

```html
<!DOCTYPE html>
<html lang="en">
<head>
<meta charset="utf-8">
<title>loma vereda – furniture and lamps</title>
<link href="https://fonts.googleapis.com/css2?family=Open+Sans:wght@400;600;700;800&display=swap" rel="stylesheet">
<style>
:root{
  --ink:#2f2b28;
  --topbar:#3b3734;
  --page:#efeeeb;
  --white:#ffffff;
  --tab:#6b645c;
  --orange:#f0831e;
  --price:#e8194b;
  --muted:#8a8580;
  --line:#dcdad6;
  --card-foot:#f6f6f5;
  --banner-panel:#5a5045;
  --footer:#7a7166;
  --footer-line:#8e867b;
  --bottom:#3a312b;
}
*{box-sizing:border-box;margin:0;padding:0}
html,body{width:1200px;height:2424px;overflow:hidden}
body{font-family:"Open Sans",Arial,sans-serif;color:var(--ink);background:var(--page);position:relative}
.abs{position:absolute}

/* top bar */
.topbar{left:0;top:0;width:1200px;height:44px;background:var(--topbar);color:#e8e6e3;font-size:12px;display:flex;align-items:center;padding:0 92px}
.topbar .welcome{flex:1}
.topbar .tools{display:flex;gap:26px;align-items:center}
.topbar .tools span{display:flex;align-items:center;gap:6px}

/* header */
.header{left:0;top:44px;width:1200px;height:122px;background:var(--white);display:flex;align-items:center;padding:0 92px}
.brand{display:flex;align-items:center;gap:12px;flex:1}
.brand-mark{width:58px;height:38px;background:var(--topbar)}
.brand-name{font-size:26px;font-weight:700;color:var(--orange);letter-spacing:-.5px}
.nav{display:flex;gap:30px;font-size:13px;font-weight:700;margin-right:34px}
.search{width:230px;height:30px;border:1px solid var(--line);display:flex;align-items:center;justify-content:flex-end;padding:0 12px;font-size:10px;color:#a5a19c;gap:34px}

/* hero */
.hero{left:80px;top:168px;width:1040px;height:366px;background:linear-gradient(90deg,#6d513b 0%,#b08a66 30%,#8d6a4b 55%,#5d5046 70%)}
.hero-panel{left:647px;top:0;width:393px;height:366px;background:rgba(70,60,55,.7);color:var(--white);padding:70px 38px 0 40px}
.hero-panel h1{font-size:35px;font-weight:700;letter-spacing:.5px}
.hero-panel .rule{width:266px;height:2px;background:#ddd;margin:16px 0 24px}
.hero-panel p{font-size:12px;line-height:20px;text-align:right;width:312px}
.btn-outline{display:inline-block;margin:36px 0 0 90px;border:2px solid var(--white);padding:8px 14px;font-size:12px;font-weight:700}

/* section heading tabs */
.tab-head{height:42px;border-bottom:1px solid var(--line);display:flex}
.tab-head span{background:var(--tab);color:var(--white);font-size:15px;font-weight:700;padding:0 18px;display:flex;align-items:center;text-transform:uppercase}

.featured{left:80px;top:560px;width:1040px}
.grid{left:80px;top:626px;width:1040px;display:grid;grid-template-columns:repeat(4,240px);column-gap:26.6px;row-gap:40px}
.card{height:384px;background:var(--white);display:flex;flex-direction:column}
.card .shot{height:224px;display:flex;align-items:center;justify-content:center}
.card .shot div{width:160px;height:170px;border-radius:6px}
.card .info{flex:1;background:var(--card-foot);text-align:center;padding-top:18px}
.card h3{font-size:12.5px;font-weight:700}
.card .price{color:var(--price);font-size:17px;font-weight:700;margin:12px 0 6px}
.card .desc{font-size:8.5px;line-height:11px;color:var(--muted);width:150px;margin:0 auto}
.buy{display:flex;justify-content:center;margin-top:14px}
.buy .label{width:82px;height:34px;background:var(--white);border:1px solid #e6e4e1;font-size:10px;font-weight:700;color:#a7a29c;display:flex;align-items:center;justify-content:center}
.buy .cart{width:36px;height:34px;background:var(--orange);margin-left:8px;display:flex;align-items:center;justify-content:center}

/* banner */
.banner{left:80px;top:1480px;width:1040px;height:126px;background:linear-gradient(90deg,#8b7a5c,#c0ad8a 40%,#7b6b53 75%)}
.banner-panel{left:800px;top:0;width:240px;height:126px;background:var(--banner-panel);color:var(--white);text-align:center;padding-top:22px}
.banner-panel h2{font-size:25px;font-weight:700;letter-spacing:-.3px}
.banner-panel p{font-size:11px;margin-top:0}
.banner-panel .link{font-size:10px;font-weight:700;margin-top:22px}

/* lower three columns */
.lower{left:0;top:1610px;width:1200px;height:440px;background:var(--white)}
.col{top:1656px;width:312px}
.col .tab-head span{font-size:14px}
.post{padding:16px 0 18px;border-bottom:1px solid var(--line)}
.post:last-child{border-bottom:none}
.post h4{font-size:11.5px;font-weight:700;margin-top:8px}
.post .date{font-size:10px;color:#555;margin:5px 0 14px}
.post p{font-size:10px;line-height:16px;color:#444}
.post .more{font-size:10px;margin-top:14px}
.tweet{display:flex;gap:16px;padding:24px 0 26px;border-bottom:1px solid var(--line);width:310px}
.tweet:last-child{border-bottom:none}
.avatar{width:68px;height:70px;background:linear-gradient(180deg,#d8d3cc,#b9aea2);flex:none}
.tweet .body{font-size:9.5px;line-height:16px;color:#333}
.tweet b{font-weight:700}
.tweet .handle{color:var(--orange)}
.tweet .rt{margin-top:12px}
.video{margin-top:30px;width:312px;height:248px;background:linear-gradient(160deg,#c7c2ba,#7c6a55 55%,#4f4236);display:flex;align-items:center;justify-content:center}

/* footer */
.footer{left:0;top:2050px;width:1200px;height:288px;background:var(--footer);color:#f3f1ee}
.fcol{top:2106px}
.fcol h5{font-size:13px;font-weight:700;padding-bottom:20px;border-bottom:1px solid var(--footer-line);margin-bottom:18px;text-transform:uppercase}
.fcol ul{list-style:none;font-size:12px;line-height:25px}
.fcol.small ul{font-size:10.5px;line-height:25px}
.fcol p{font-size:10px;line-height:20px}
.cards{display:flex;gap:8px;margin-top:16px}
.cards div{width:44px;height:26px;background:var(--white);border-radius:2px}
.subscribe{display:flex;margin-top:36px}
.subscribe .field{width:168px;height:32px;background:var(--white);font-size:10px;color:#999;display:flex;align-items:center;justify-content:center}
.subscribe .go{width:78px;height:32px;background:var(--orange);color:var(--white);font-size:11px;font-weight:700;display:flex;align-items:center;justify-content:center}

.bottom{left:0;top:2338px;width:1200px;height:86px;background:var(--bottom);color:#eee;font-size:12px;display:flex;align-items:center;padding:0 76px}
.bottom .copy{flex:1}
.bottom .links{display:flex;gap:22px;margin-right:60px}
.bottom .social{display:flex;gap:8px}
.bottom .social i{width:20px;height:20px;border-radius:50%;background:#f2f0ed;display:block}
</style>
</head>
<body>

<div class="abs topbar">
  <div class="welcome">Mara Lindqvist, welcome to our online store!</div>
  <div class="tools">
    <span><svg width="11" height="11" viewBox="0 0 12 12"><circle cx="6" cy="6" r="4.5" fill="none" stroke="#e8e6e3" stroke-width="2"/></svg>Setting ⌄</span>
    <span><svg width="11" height="11" viewBox="0 0 12 12"><circle cx="6" cy="3.5" r="3" fill="#e8e6e3"/><path d="M0 12a6 5 0 0 1 12 0z" fill="#e8e6e3"/></svg>My Account ⌄</span>
    <span><svg width="13" height="11" viewBox="0 0 14 12"><path d="M0 1h3l2 7h7l2-5H4" fill="none" stroke="#e8e6e3" stroke-width="1.5"/><circle cx="6" cy="10.5" r="1.3" fill="#e8e6e3"/><circle cx="11" cy="10.5" r="1.3" fill="#e8e6e3"/></svg>Cart: 0 item</span>
  </div>
</div>

<header class="abs header">
  <div class="brand"><div class="brand-mark"></div><div class="brand-name">loma vereda</div></div>
  <nav class="nav"><span>HOME</span><span>CATEGORIES</span><span>ABOUT US</span><span>FAQs</span><span>CONTACT US</span></nav>
  <div class="search">search your item here
    <svg width="11" height="11" viewBox="0 0 12 12"><circle cx="5" cy="5" r="3.8" fill="none" stroke="#999" stroke-width="1.5"/><path d="M8 8l3 3" stroke="#999" stroke-width="1.5"/></svg>
  </div>
</header>

<section class="abs hero" role="img" aria-label="Bedroom with upholstered bed, bedside table, vase and wooden tile wall">
  <div class="abs hero-panel">
    <h1>LOREM IPSUMEI</h1>
    <div class="rule"></div>
    <p>aspernatur magni quae aperiam aut veritatis beatae eos aut voluptas doloremque perspiciatis error natus natus aut eaque inventore quasi consequuntur consequuntur ipsa aspernatur iste sit</p>
    <span class="btn-outline">VIEW MORE</span>
  </div>
</section>

<div class="abs featured"><div class="tab-head"><span>Featured Products</span></div></div>

<main class="abs grid">
  <article class="card"><div class="shot"><div role="img" aria-label="Painted vintage chest of drawers" style="background:linear-gradient(135deg,#b84a3a,#3f7f8a,#c89a3a)"></div></div><div class="info"><h3>VOLUPTATEM FUGIT AUT</h3><div class="price">$856.00</div><p class="desc">ut enim rem ipsum quasi voluptatem doloremque qui ad eaque</p><div class="buy"><span class="label">BUY NOW</span><span class="cart"><svg width="14" height="12" viewBox="0 0 14 12"><path d="M0 1h3l2 7h7l2-5H4" fill="none" stroke="#fff" stroke-width="1.6"/><circle cx="6" cy="10.5" r="1.3" fill="#fff"/><circle cx="11" cy="10.5" r="1.3" fill="#fff"/></svg></span></div></div></article>
  <article class="card"><div class="shot"><div role="img" aria-label="Reclaimed wood dining table" style="background:linear-gradient(180deg,#8a6a4a,#5e8c8a 40%,#6b4a32);height:90px"></div></div><div class="info"><h3>VOLUPTATEM FUGIT AUT</h3><div class="price">$856.00</div><p class="desc">ut enim rem ipsum quasi voluptatem doloremque qui ad eaque</p><div class="buy"><span class="label">BUY NOW</span><span class="cart"><svg width="14" height="12" viewBox="0 0 14 12"><path d="M0 1h3l2 7h7l2-5H4" fill="none" stroke="#fff" stroke-width="1.6"/><circle cx="6" cy="10.5" r="1.3" fill="#fff"/><circle cx="11" cy="10.5" r="1.3" fill="#fff"/></svg></span></div></div></article>
  <article class="card"><div class="shot"><div role="img" aria-label="Grey rattan table with chairs" style="background:linear-gradient(180deg,#777,#4a4a4a);height:110px"></div></div><div class="info"><h3>VOLUPTATEM FUGIT AUT</h3><div class="price">$856.00</div><p class="desc">ut enim rem ipsum quasi voluptatem doloremque qui ad eaque</p><div class="buy"><span class="label">BUY NOW</span><span class="cart"><svg width="14" height="12" viewBox="0 0 14 12"><path d="M0 1h3l2 7h7l2-5H4" fill="none" stroke="#fff" stroke-width="1.6"/><circle cx="6" cy="10.5" r="1.3" fill="#fff"/><circle cx="11" cy="10.5" r="1.3" fill="#fff"/></svg></span></div></div></article>
  <article class="card"><div class="shot"><div role="img" aria-label="Tall painted vintage cabinet" style="background:linear-gradient(180deg,#7a4a2a,#a68a4a,#5a7a5a);width:96px;height:200px"></div></div><div class="info"><h3>VOLUPTATEM FUGIT AUT</h3><div class="price">$856.00</div><p class="desc">ut enim rem ipsum quasi voluptatem doloremque qui ad eaque</p><div class="buy"><span class="label">BUY NOW</span><span class="cart"><svg width="14" height="12" viewBox="0 0 14 12"><path d="M0 1h3l2 7h7l2-5H4" fill="none" stroke="#fff" stroke-width="1.6"/><circle cx="6" cy="10.5" r="1.3" fill="#fff"/><circle cx="11" cy="10.5" r="1.3" fill="#fff"/></svg></span></div></div></article>
  <article class="card"><div class="shot"><div role="img" aria-label="Round rattan dining set" style="background:linear-gradient(180deg,#c49a6a,#8a6040);height:120px"></div></div><div class="info"><h3>VOLUPTATEM FUGIT AUT</h3><div class="price">$856.00</div><p class="desc">ut enim rem ipsum quasi voluptatem doloremque qui ad eaque</p><div class="buy"><span class="label">BUY NOW</span><span class="cart"><svg width="14" height="12" viewBox="0 0 14 12"><path d="M0 1h3l2 7h7l2-5H4" fill="none" stroke="#fff" stroke-width="1.6"/><circle cx="6" cy="10.5" r="1.3" fill="#fff"/><circle cx="11" cy="10.5" r="1.3" fill="#fff"/></svg></span></div></div></article>
  <article class="card"><div class="shot"><div role="img" aria-label="Weathered wooden chest" style="background:linear-gradient(180deg,#a88a6a,#6a8a80,#7a5a3a);height:90px"></div></div><div class="info"><h3>VOLUPTATEM FUGIT AUT</h3><div class="price">$856.00</div><p class="desc">ut enim rem ipsum quasi voluptatem doloremque qui ad eaque</p><div class="buy"><span class="label">BUY NOW</span><span class="cart"><svg width="14" height="12" viewBox="0 0 14 12"><path d="M0 1h3l2 7h7l2-5H4" fill="none" stroke="#fff" stroke-width="1.6"/><circle cx="6" cy="10.5" r="1.3" fill="#fff"/><circle cx="11" cy="10.5" r="1.3" fill="#fff"/></svg></span></div></div></article>
  <article class="card"><div class="shot"><div role="img" aria-label="Brass floor lamp with cream shade" style="background:linear-gradient(180deg,#efd9a8,#d4b46a);width:90px"></div></div><div class="info"><h3>VOLUPTATEM FUGIT AUT</h3><div class="price">$856.00</div><p class="desc">ut enim rem ipsum quasi voluptatem doloremque qui ad eaque</p><div class="buy"><span class="label">BUY NOW</span><span class="cart"><svg width="14" height="12" viewBox="0 0 14 12"><path d="M0 1h3l2 7h7l2-5H4" fill="none" stroke="#fff" stroke-width="1.6"/><circle cx="6" cy="10.5" r="1.3" fill="#fff"/><circle cx="11" cy="10.5" r="1.3" fill="#fff"/></svg></span></div></div></article>
  <article class="card"><div class="shot"><div role="img" aria-label="Small vintage cabinet with glass door" style="background:linear-gradient(135deg,#5a3a2a,#8a6a4a,#3a5a7a);height:140px"></div></div><div class="info"><h3>VOLUPTATEM FUGIT AUT</h3><div class="price">$856.00</div><p class="desc">ut enim rem ipsum quasi voluptatem doloremque qui ad eaque</p><div class="buy"><span class="label">BUY NOW</span><span class="cart"><svg width="14" height="12" viewBox="0 0 14 12"><path d="M0 1h3l2 7h7l2-5H4" fill="none" stroke="#fff" stroke-width="1.6"/><circle cx="6" cy="10.5" r="1.3" fill="#fff"/><circle cx="11" cy="10.5" r="1.3" fill="#fff"/></svg></span></div></div></article>
</main>

<section class="abs banner" role="img" aria-label="Outdoor wooden table with rattan chairs on a terrace">
  <div class="abs banner-panel">
    <h2>outside furniture</h2>
    <p>big savings on quality items</p>
    <div class="link">view the collection</div>
  </div>
</section>

<div class="abs lower"></div>

<section class="abs col" style="left:80px">
  <div class="tab-head"><span>Lates from blog</span></div>
  <div class="post" style="padding-top:24px">
    <h4>LOREM IPSUM DOLOR SIT AMET REM EOS</h4>
    <div class="date">May 16, 2014</div>
    <p>Lorem ipsum dolor sit amet voluptatem fugit omnis explicabo nemo rem ipsam quasi illo dolores voluptatem doloremque</p>
    <div class="more">read more</div>
  </div>
  <div class="post">
    <h4>LOREM IPSUM DOLOR SIT AMET REM EOS</h4>
    <div class="date">May 16, 2014</div>
    <p>Lorem ipsum dolor sit amet voluptatem fugit omnis explicabo nemo rem ipsam quasi illo dolores voluptatem doloremque</p>
    <div class="more">read more</div>
  </div>
</section>

<section class="abs col" style="left:444px">
  <div class="tab-head"><span>Tweets</span></div>
  <div class="tweet">
    <div class="avatar" role="img" aria-label="Profile photo"></div>
    <div class="body"><b>Tomas Reiner</b> <span class="handle">@Mara Lindqvist</span><br>Lorem ipsum dolor sit amet voluptatem fugit aut illo omnis explicabo ipsa nemo rem ipsam<div class="rt">retweeted by <b>Ilse Brandt</b></div></div>
  </div>
  <div class="tweet">
    <div class="avatar" role="img" aria-label="Profile photo"></div>
    <div class="body"><b>Tomas Reiner</b> <span class="handle">@Mara Lindqvist</span><br>Lorem ipsum dolor sit amet voluptatem fugit aut illo omnis explicabo ipsa nemo rem ipsam<div class="rt">retweeted by <b>Ilse Brandt</b></div></div>
  </div>
</section>

<section class="abs col" style="left:808px">
  <div class="tab-head"><span>Watch video</span></div>
  <div class="video" role="img" aria-label="Video still of a wooden coffee table in a living room">
    <svg width="66" height="66" viewBox="0 0 66 66"><circle cx="33" cy="33" r="33" fill="#fff"/><path d="M26 20l20 13-20 13z" fill="#2f2b28"/></svg>
  </div>
</section>

<footer class="abs footer"></footer>
<div class="abs fcol" style="left:76px;width:152px"><h5>Company</h5><ul><li>Search</li><li>About</li><li>News</li><li>Retailers</li><li>Contact Us</li></ul></div>
<div class="abs fcol small" style="left:254px;width:152px"><h5>Shipping</h5><ul><li>Shipping Fee</li><li>Order and Returns</li><li>Track Order</li><li>Search Term</li><li>Site Map</li></ul></div>
<div class="abs fcol small" style="left:432px;width:152px"><h5>FAQs</h5><ul><li>Customer Service</li><li>Privacy Policy</li><li>Term and Use</li><li>My Account</li><li>Others</li></ul></div>
<div class="abs fcol" style="left:610px;width:228px"><h5>Payment Method</h5><p>Lorem ipsum dolor sit amet voluptatem fugit aut omnis explicaboneno rem ipsam quasi illo voluptatem doloremque</p><div class="cards"><div></div><div></div><div></div><div></div></div></div>
<div class="abs fcol" style="left:876px;width:246px"><h5 style="border-bottom:none;padding-bottom:0">News &amp; Updates</h5><p>Sign up to get the latest on sales, new releases and more ...</p><div class="subscribe"><span class="field">enter your email here</span><span class="go">SIGN UP</span></div></div>

<div class="abs bottom">
  <div class="copy">© 2014 <b>loma vereda</b></div>
  <div class="links"><span>About us</span><span>privacy policy</span><span>terms and use</span><span>Careers</span><span>Countries</span><span>contact us</span></div>
  <div class="social"><i></i><i></i><i></i><i></i><i></i></div>
</div>

</body>
</html>
```